Brightwave Reach - Business Card

We need a business card for a Social Media Marketing company that specializes in online marketing for small businesses in Canada using common Social Media platforms such as Pixlora, Chatterly, Blinkpost & Quibber.

I have uploaded a copy of our logo which I would like utilized in the business card. We would like the business card to be modern yet classy design.

Our website is www.brightwavereach.ca

Industry/Entity Type

Marketing

Contact Information for Business Card

Email: info@brightwavereach.ca
Website: www.brightwavereach.ca
Telephone: 604-555-0193

Colors

Designer to choose colors to be used in the design.

Requirements
Must have
• Social Media icons on reverse
• Please add some designs with color.

```html
<!DOCTYPE html>
<html lang="en">
<head>
<meta charset="utf-8">
<title>Brightwave Reach – Business Card</title>
<link rel="stylesheet" href="https://fonts.googleapis.com/css2?family=Questrial&display=swap">
<style>
  :root {
    --page: #e9e9e7;
    --ink: #3b3d3f;
    --ink-dark: #2e3032;
    --slate-1: #4a4e50;
    --slate-2: #5d6264;
    --slate-3: #3a3d3f;
    --paper-1: #ffffff;
    --paper-2: #e6e7e8;
    --grey-mid: #9a9c9e;
    --on-dark: #f2f2f2;
  }
  * { box-sizing: border-box; margin: 0; padding: 0; }
  html, body {
    width: 1200px; height: 784px; overflow: hidden;
    background: var(--page);
    font-family: "Questrial", "Century Gothic", sans-serif;
  }
  .canvas { position: relative; width: 1200px; height: 784px; }

  .card {
    position: absolute; width: 540px; height: 309px;
    overflow: hidden; border-radius: 3px;
    box-shadow: 0 6px 18px rgba(0,0,0,.18);
  }
  .card-front { left: 50px; top: 90px; }
  .card-back  { left: 610px; top: 385px; }

  .facet-texture { position: absolute; inset: 0; }
  .card-front .facet-texture {
    background: radial-gradient(ellipse at 60% 30%, var(--slate-2), var(--slate-1) 55%, var(--slate-3));
  }
  .card-back .facet-texture {
    background: radial-gradient(ellipse at 70% 20%, var(--paper-1), #f3f3f3 50%, var(--paper-2));
  }

  .wordmark {
    position: absolute; text-align: center; text-transform: uppercase;
    line-height: 1; letter-spacing: 1px;
  }
  .card-front .wordmark {
    left: 0; right: 0; top: 92px; font-size: 40px; color: var(--on-dark);
  }
  .card-back .wordmark {
    left: 60px; width: 250px; top: 62px; font-size: 34px; color: var(--ink);
  }

  .social-list {
    position: absolute; left: 0; right: 0; top: 222px;
    display: flex; justify-content: center; gap: 18px;
    list-style: none;
  }
  .social-list li {
    display: flex; align-items: center; gap: 6px;
    font-size: 13px; color: var(--on-dark);
  }
  .social-list .dot {
    width: 16px; height: 16px; border-radius: 4px; background: var(--on-dark);
  }

  .contact-list {
    position: absolute; left: 34px; top: 196px; list-style: none;
  }
  .contact-list li {
    display: flex; align-items: center; gap: 12px;
    font-size: 15px; color: var(--ink-dark); height: 25px;
  }
  .contact-list svg { width: 15px; height: 15px; fill: var(--ink-dark); }

  .accent { position: absolute; }
</style>
</head>
<body>
<main class="canvas">

  <section class="card card-front" aria-label="Card front">
    <div class="facet-texture" role="img" aria-label="Dark slate faceted low-poly texture"></div>
    <h1 class="wordmark">Brightwave<br>Reach</h1>
    <ul class="social-list">
      <li><span class="dot"></span>Pixlora</li>
      <li><span class="dot"></span>Chatterly</li>
      <li><span class="dot"></span>Quibber</li>
    </ul>
  </section>

  <section class="card card-back" aria-label="Card back">
    <div class="facet-texture" role="img" aria-label="Light grey faceted low-poly texture"></div>
    <h2 class="wordmark">Brightwave<br>Reach</h2>

    <svg class="accent" width="540" height="309" viewBox="0 0 540 309" aria-hidden="true">
      <polygon points="250,200 540,184 540,192 246,209" fill="var(--ink)"/>
      <polygon points="0,292 116,286 112,296 0,302" fill="var(--ink-dark)"/>
      <polygon points="120,286 170,283 166,293 116,296" fill="var(--grey-mid)"/>
    </svg>

    <ul class="contact-list">
      <li>
        <svg viewBox="0 0 24 24"><path d="M6.6 10.8a15 15 0 0 0 6.6 6.6l2.2-2.2a1 1 0 0 1 1-.25 11 11 0 0 0 3.6.6 1 1 0 0 1 1 1V20a1 1 0 0 1-1 1A17 17 0 0 1 3 4a1 1 0 0 1 1-1h3.5a1 1 0 0 1 1 1c0 1.25.2 2.45.6 3.6a1 1 0 0 1-.25 1z"/></svg>
        604-555-0193
      </li>
      <li>
        <svg viewBox="0 0 24 24"><path d="M2 5h20v14H2z M4 7v.5l8 5 8-5V7z" fill-rule="evenodd"/></svg>
        info@brightwavereach.ca
      </li>
      <li>
        <svg viewBox="0 0 24 24"><path d="M12 2a10 10 0 1 0 0 20 10 10 0 0 0 0-20zm-1 2.1V8H7.3A8 8 0 0 1 11 4.1zm2 0A8 8 0 0 1 16.7 8H13zM5.3 10H11v4H5.3a8 8 0 0 1 0-4zm7.7 0h5.7a8 8 0 0 1 0 4H13zm-5.7 6H11v3.9A8 8 0 0 1 7.3 16zm5.7 0h3.7a8 8 0 0 1-3.7 3.9z"/></svg>
        www.brightwavereach.ca
      </li>
    </ul>
  </section>

</main>
</body>
</html>
```